Bright Trails, Strong Spirits Poster for American Indian Older Adults

We need am 11" x 17" poster designed for a health outreach project designed to reach older U.S. American Indians. The materials developed through this project will be distributed to American Indian and Alaska Native tribes, communities and tribal-serving organizations across the U.S. (more than 500 different tribes). If we find a successful design we will work with that designer to produce at least one other item we need design work for using the same look/feel and maybe other materials for this project. (more work!). The poster will include a set of facts (bulleted list on the attached document) that we would like presented in an "infographic" style. The design must be reflective of the American Indian culture and designed with older adults (65 and older) in mind. Imagery plays a strong role in the American Indian culture in the U.S. images of the heart, water, feathers, circle of life, etc. If you use photos of people they must include older adults and they must be American Indian (Native American). We prefer deep earth tones for the color scheme. The design must take into account design principles for older adults: 1. Try not to put colored font on colored background 2. Ensure high contrast for text 3. Font style should be sans serif, not cursive,decorative or heavily stylized because it is harder to read 4. Avoid using all caps 5. Don't print sideways or on top of images, shaded, backgrounds, etc. 6. All images should related specifically to the content of the text and be culturally appropriate for both older adults and American Indians. The final design should be easy to read and appeal to older American Indian adults. We need to incorporate three logos on the poster towards the bottom they should not be the center/focus of the poster. We also need to include a statement about who produced the materials- that can be very small below the logos at the bottom of the poster. We've attached the text for the poster and three logo files (note one is solid blue- we will finalize that after the document design is selected but need a placeholder for that logo.

Target Market(s)

Older adult (65 and older) American Indian and Alaska Natives and their family members in tribes, communities and tribal-serving organizations across the US

Font styles to use
Sans Serif

Requirements
Must have
• Must adhere to good design principles for older adults (listed in project description)
• Must feature culturally appropriate/targeted imagery and design look and feel

```html
<!DOCTYPE html>
<html lang="en">
<head>
<meta charset="utf-8">
<title>Bright Trails, Strong Spirits</title>
<link href="https://fonts.googleapis.com/css2?family=Montserrat:wght@700;800&family=Open+Sans:ital,wght@0,400;0,600;0,700;1,600&display=swap" rel="stylesheet">
<style>
  :root {
    --ink-brown: #3b2620;
    --crimson: #8e1b2e;
    --earth-deep: #241609;
    --white: #ffffff;
    --cream-icon: #f3e6cf;
    --dash: #d8cfc3;
    --footer-bg: #ffffff;
    --footer-ink: #5a4a3e;
    --partner-red: #d4452a;
    --partner-green: #2f8a3a;
    --partner-blue: #2a5da8;
  }
  * { box-sizing: border-box; margin: 0; padding: 0; }
  html, body { width: 775px; height: 1200px; overflow: hidden; background: var(--white); }
  .poster {
    position: relative;
    width: 775px;
    height: 1200px;
    overflow: hidden;
    font-family: "Open Sans", Arial, sans-serif;
    color: var(--white);
  }
  .scene-photo {
    position: absolute;
    left: 0; top: 0;
    width: 775px; height: 1145px;
    background:
      radial-gradient(ellipse 260px 560px at 585px 760px, rgba(30,18,8,0.85), rgba(30,18,8,0) 70%),
      linear-gradient(180deg, #f6e4bd 0%, #e9c98f 18%, #c99a5a 32%, #8d6232 44%, #6a4622 58%, #4d3218 75%, var(--earth-deep) 100%);
  }
  .elder-portrait {
    position: absolute;
    left: 150px; top: 150px;
    width: 420px; height: 420px;
    border-radius: 50%;
    background: radial-gradient(circle, rgba(255,244,220,0.28), rgba(255,244,220,0) 70%);
  }
  .pattern-band {
    position: absolute;
    left: 0; top: 0;
    width: 775px; height: 46px;
    background: repeating-linear-gradient(90deg, #d9b58a 0 40px, #c99c6b 40px 80px);
  }
  .headline {
    position: absolute;
    left: 18px; top: 58px;
    font-family: "Montserrat", Arial, sans-serif;
    font-weight: 800;
    font-size: 66px;
    line-height: 72px;
    letter-spacing: -1px;
    color: var(--ink-brown);
  }
  .subhead {
    position: absolute;
    left: 18px; top: 210px;
    font-family: "Montserrat", Arial, sans-serif;
    font-weight: 700;
    font-size: 26.5px;
    line-height: 33px;
    color: var(--crimson);
  }
  .intro {
    position: absolute;
    left: 18px; top: 440px;
    width: 352px;
    font-weight: 700;
    font-size: 18px;
    line-height: 25px;
  }
  .fact { position: absolute; left: 22px; width: 400px; }
  .fact-icon { position: absolute; left: 0; top: 0; }
  .fact-icon.placeholder { background: var(--cream-icon); opacity: 0.9; border-radius: 6px; }
  .fact-text { position: absolute; left: 88px; top: 0; width: 310px; }
  .fact-figure {
    font-family: "Montserrat", Arial, sans-serif;
    font-weight: 700;
    font-size: 32px;
    line-height: 34px;
  }
  .fact-label { font-size: 15.5px; line-height: 18px; }
  .fact-1 { top: 590px; }
  .fact-2 { top: 684px; }
  .fact-3 { top: 790px; }
  .fact-4 { top: 888px; }
  .divider {
    position: absolute;
    left: 108px; top: 1008px;
    width: 278px; height: 6px;
    border-top: 6px dashed var(--dash);
  }
  .call-to-action {
    position: absolute;
    left: 108px; top: 1028px;
    width: 285px;
    font-style: italic;
    font-weight: 600;
    font-size: 16.5px;
    line-height: 23px;
  }
  .footer {
    position: absolute;
    left: 0; top: 1145px;
    width: 775px; height: 55px;
    background: var(--footer-bg);
    padding: 8px 0 0 26px;
  }
  .partners {
    display: flex;
    align-items: center;
    gap: 28px;
    font-family: "Montserrat", Arial, sans-serif;
    font-weight: 700;
  }
  .partner { display: flex; align-items: center; gap: 8px; font-size: 17px; }
  .partner-north { color: var(--partner-red); }
  .partner-circle { color: var(--partner-green); font-size: 14px; }
  .partner-mark { width: 12px; height: 12px; border-radius: 50%; background: currentColor; }
  .partner-badge { width: 64px; height: 22px; background: var(--partner-blue); }
  .producer-note {
    margin-top: 5px;
    font-size: 10px;
    line-height: 12px;
    color: var(--footer-ink);
  }
</style>
</head>
<body>
  <main class="poster">
    <div class="scene-photo" role="img" aria-label="Sepia photograph of an elderly American Indian couple seen from behind standing on a sandy shore by the water"></div>
    <div class="elder-portrait" role="img" aria-label="Faint portrait of an elder in a feathered headdress blended into the sky"></div>
    <div class="pattern-band" role="img" aria-label="Woven American Indian border pattern in earth tones"></div>

    <h1 class="headline">Bright Trails,<br>Strong Spirits …</h1>
    <p class="subhead">The River of Life Flows<br>Through the Heart,<br>Protecting the Mind and Body</p>

    <p class="intro">Elders with diabetes, heart disease, or high blood pressure have a much higher risk of developing Alzheimer’s or other dementias</p>

    <section class="fact fact-1">
      <div class="fact-icon placeholder" role="img" aria-label="Map of the United States" style="width:72px;height:48px;top:2px;"></div>
      <div class="fact-text">
        <div class="fact-figure">5.7 Million</div>
        <div class="fact-label">Americans have<br>Alzheimer’s disease</div>
      </div>
    </section>

    <section class="fact fact-2">
      <svg class="fact-icon" width="62" height="62" viewBox="0 0 62 62" aria-hidden="true">
        <path d="M31 56 L7 30 C-2 20 6 5 18 6 C24 6 28 10 31 15 C34 10 38 6 44 6 C56 5 64 20 55 30 Z" fill="none" stroke="var(--white)" stroke-width="2.5" stroke-linejoin="round"/>
        <polyline points="4,31 20,31 25,22 31,42 36,27 40,31 58,31" fill="none" stroke="var(--white)" stroke-width="2.5" stroke-linejoin="round"/>
      </svg>
      <div class="fact-text">
        <div class="fact-label">Alzheimer’s is the</div>
        <div class="fact-figure">6th</div>
        <div class="fact-label">leading cause of Death</div>
      </div>
    </section>

    <section class="fact fact-3">
      <div class="fact-icon placeholder" role="img" aria-label="Pyramid of ten small people figures" style="width:60px;height:62px;top:-6px;"></div>
      <div class="fact-text">
        <div class="fact-figure">1 in 10</div>
        <div class="fact-label">People age 65 and older<br>has Alzheimer’s</div>
      </div>
    </section>

    <section class="fact fact-4">
      <div class="fact-icon placeholder" role="img" aria-label="Illustration of an elder wearing a feathered headdress, in profile" style="width:62px;height:64px;top:-4px;"></div>
      <div class="fact-text">
        <div class="fact-figure">1 in 3</div>
        <div class="fact-label">American Indians over 65<br>develop dementia, including<br>Alzheimer’s</div>
      </div>
    </section>

    <div class="divider"></div>
    <p class="call-to-action">Make an appointment with your doctor today to talk about how to keep your mind and heart healthy.</p>

    <footer class="footer">
      <div class="partners">
        <div class="partner partner-north"><span class="partner-mark"></span>Northwind Health</div>
        <div class="partner partner-circle"><span class="partner-mark"></span>Circle of Elders Alliance</div>
        <div class="partner-badge" role="img" aria-label="Partner logo placeholder"></div>
      </div>
      <p class="producer-note">Produced by Northwind Health in partnership with Circle of Elders Alliance.</p>
    </footer>
  </main>
</body>
</html>
```